Lotus Ridge Website

We need a website that has clean, asian looking images that relax and motivate people to come into our integrated medical center. My current website is www.needlecalmharbor.com and I would like the design for Lotus Ridge Wellness Partners to be similar but more inviting with video content and a product purchase store as well. A moving banner would be nice too. When people are looking for ways of losing weight or getting out of pain we want them to make the connection that we have the solution. This website needs to provide sufficient information so that patients are well informed and choose us as their health provider before they ever walk through our doors. We offer comprehensive natural medicine that is based on the principles that the body can heal itself when given the right conditions. Our services include medical weight loss and hormone balancing, acupuncture and chinese herbal medicine, physical medicine, trigger point injections, allergy testing and joint rehabilitation. The Medical Doctor and Licensed Acupuncturist work as a team to provide optimal care that is catered to each individual who comes through our doors.
Updates

Target Market(s)

40 to 50 year olds who want to lose weight or have pain issues.

Industry/Entity Type

Medical

Requirements
Must have
• Use photos from our website www.needlecalmharbor.com or similar content. Video content. Moving banner with relaxing images.
Nice to have
• Happy, healthy looking people. Medical Doctors working as a team. Friendly staff in a cutting edge facility.
Should not have
• Papyrus font, or big bold words.

```html
<!DOCTYPE html>
<html lang="en">
<head>
<meta charset="utf-8">
<title>Lotus Ridge Website</title>
<link href="https://fonts.googleapis.com/css2?family=Carlito:wght@400;700&family=Arimo:wght@400&display=swap" rel="stylesheet">
<style>
:root{
  --olive-dark:#5f6420;
  --olive:#7c8232;
  --olive-light:#8e9440;
  --nav-active:#8dbf3f;
  --page:#f3f4f5;
  --heading:#3c5877;
  --text:#3d3d3d;
  --link-olive:#6f6a1e;
  --button-olive:#5c5a1e;
  --footer:#262626;
  --footer-text:#c9c9c9;
  --rule:#d3d5d8;
}
*{box-sizing:border-box;margin:0;padding:0}
html,body{width:969px;height:1200px;overflow:hidden}
body{position:relative;background:var(--page);font-family:"Carlito",Calibri,sans-serif;color:var(--text)}
.abs{position:absolute}
.header-band{left:0;top:0;width:969px;height:295px;background:linear-gradient(180deg,var(--olive-dark) 0%,var(--olive) 55%,var(--olive-light) 100%);border-bottom:2px solid #d8d9c8}
.brand{left:37px;top:10px;width:86px;height:118px;display:flex;flex-direction:column;align-items:center;justify-content:center;gap:8px}
.brand-mark{width:40px;height:40px;background:#fff}
.brand-name{color:#fff;font-size:15px;font-weight:700;text-align:center;line-height:1.1}
.main-nav a{position:absolute;top:31px;color:#fff;font-size:13px;font-weight:700;text-decoration:none;text-shadow:0 1px 2px rgba(0,0,0,.5)}
.main-nav .active{top:20px;left:295px;width:57px;height:38px;line-height:38px;text-align:center;background:linear-gradient(#9fd04e,#77aa2f);border:1px solid #b7df7a;box-shadow:0 1px 3px rgba(0,0,0,.35)}
.account{left:545px;top:110px;color:#fff;font-size:12.5px;font-weight:700;text-shadow:0 1px 1px rgba(0,0,0,.4)}
.account-sep{left:612px;top:109px;color:#fff;font-size:13px}
.checkout{left:623px;top:106px;width:67px;height:23px;border-radius:4px;background:linear-gradient(#fff,#e4e4e4);border:1px solid #b9b9a0;font-size:12.5px;color:#333;text-align:center;line-height:21px}
.search{left:716px;top:106px;width:165px;height:23px;background:#fff;border:1px solid #c9c9b5;border-radius:2px;font-size:10.5px;font-style:italic;color:#999;padding:5px 10px}
.banner{left:88px;top:145px;width:792px;height:268px;background:linear-gradient(90deg,#e3e6e9 0%,#f4f5f7 45%,#eef0f1 80%,#e6e3e1 100%);box-shadow:0 14px 18px -6px rgba(0,0,0,.35)}
.banner-text{left:213px;top:196px;width:500px;font-family:"Arimo",Arial,sans-serif;font-size:20px;line-height:30px;color:#333}
.banner-btn{top:372px;width:31px;height:30px;background:#6f7072;border-radius:2px}
.welcome{left:34px;top:458px;font-size:22px;color:var(--heading)}
.subhead{font-size:15px;color:var(--heading)}
.intro{left:35px;top:518px;width:538px;font-size:12.5px;line-height:18.5px;text-align:justify}
.video{left:613px;top:470px;width:306px;height:173px;background:#0d0d0d;border-radius:3px;box-shadow:0 6px 10px rgba(0,0,0,.35)}
.video-still{left:619px;top:476px;width:294px;height:148px;background:linear-gradient(120deg,#cfd3d8,#b9a79a 55%,#8f8a86)}
.wide{left:35px;top:701px;width:902px;font-size:12.5px;line-height:18px;text-indent:6px}
.cond{font-size:12.5px;color:var(--text)}
.cond::before{content:"";display:inline-block;width:5px;height:5px;border-right:1.5px solid #444;border-top:1.5px solid #444;transform:rotate(45deg);margin-right:8px;vertical-align:2px}
.rule{left:34px;top:902px;width:901px;height:1px;background:var(--rule)}
.store-title{left:34px;top:916px;font-size:16px;color:var(--heading)}
.product-img{top:958px;width:120px;height:100px;border:1px solid #c8c8c8;background:#fff;padding:8px}
.product-img span{display:block;width:100%;height:100%}
.product-title{top:966px;font-size:12.5px;font-weight:700;color:#222}
.product-text{top:992px;font-size:12.5px;line-height:19px;width:165px}
.view{top:1034px;font-size:12.5px;color:var(--link-olive)}
.buy{top:1033px;width:76px;height:20px;background:var(--button-olive);color:#fff;font-size:12.5px;text-align:center;line-height:20px;box-shadow:0 1px 2px rgba(0,0,0,.3)}
.footer{left:0;top:1087px;width:969px;height:113px;background:var(--footer);border-top:3px solid #9a9a9a}
.footer-links{left:0;top:1109px;width:969px;text-align:center;font-size:11px;color:var(--footer-text)}
.footer-links span{margin:0 5px}
.pay{top:1150px;width:27px;height:17px;background:#e6e6e6;border-radius:2px}
.copy{left:320px;top:1151px;font-size:11px;color:var(--footer-text)}
.social{top:1148px;width:22px;height:22px;border-radius:50%;background:#f2f2f2}
</style>
</head>
<body>
<div class="abs header-band"></div>
<div class="abs brand"><span class="brand-mark"></span><span class="brand-name">Lotus Ridge</span></div>
<nav class="main-nav">
  <a style="left:151px">Home</a>
  <a style="left:217px">SO Tai Ho</a>
  <a class="active">Service</a>
  <a style="left:376px">Seitai Shinpo</a>
  <a style="left:481px">Acupuncture</a>
  <a style="left:585px">Biography</a>
  <a style="left:674px">Nutrition</a>
  <a style="left:758px">My Journey</a>
  <a style="left:855px">Contact Us</a>
</nav>
<div class="abs account">My Account</div>
<div class="abs account-sep">|</div>
<div class="abs checkout">Check Out</div>
<div class="abs search">Search
  <svg class="abs" style="right:6px;top:6px" width="10" height="10" viewBox="0 0 10 10"><circle cx="4" cy="4" r="3" fill="none" stroke="#aaa" stroke-width="1.3"/><line x1="6.2" y1="6.2" x2="9" y2="9" stroke="#aaa" stroke-width="1.3"/></svg>
</div>

<div class="abs banner" role="img" aria-label="Slide photo: slim woman measuring her waist beside an apple and tape measure"></div>
<p class="abs banner-text">Excepteur sint occaecat cupidatat non proident, sunt in culpa qui officia deserunt</p>
<div class="abs banner-btn" style="left:102px"><svg width="31" height="30"><polyline points="18,10 13,15 18,20" fill="none" stroke="#fff" stroke-width="2.2"/></svg></div>
<div class="abs banner-btn" style="left:140px"><svg width="31" height="30"><polyline points="13,10 18,15 13,20" fill="none" stroke="#fff" stroke-width="2.2"/></svg></div>

<h1 class="abs welcome" style="font-weight:400">Welcome to our site</h1>
<h2 class="abs subhead" style="left:34px;top:494px;font-weight:400">How does acupuncture work?</h2>
<p class="abs intro">As the needles are carefully inserted into acupuncture points, specific cells stimulate nerve pathways that trigger a healing response to a particular organ system or area of the body.&nbsp; Acupuncture also acts on the autonomic nervous system and causes the release of endorphins, enkephalins and other natural pain relieving chemicals.&nbsp; At Lotus Ridge Acupuncture the system of acupuncture used is called Seitai Shinpo (which translates into “correct posture acupuncture method”) that uses acupuncture and moxibustion to balance structural distortions by releasing tense areas of contraction along the spine.&nbsp; When the structure is properly balanced then the body will heal much quicker.</p>

<div class="abs video"></div>
<div class="abs video-still" role="img" aria-label="Video still: patient receiving acupuncture treatment"></div>
<svg class="abs" style="left:613px;top:470px" width="306" height="173">
  <circle cx="154" cy="79" r="19" fill="#444" fill-opacity=".75" stroke="#ddd" stroke-width="2"/>
  <polygon points="148,70 148,88 163,79" fill="#fff"/>
  <rect x="12" y="159" width="2" height="7" fill="#ddd"/><rect x="16" y="159" width="2" height="7" fill="#ddd"/>
  <rect x="26" y="161" width="240" height="3" fill="#555"/>
  <rect x="270" y="161" width="24" height="3" fill="#666"/>
</svg>

<h2 class="abs subhead" style="left:34px;top:674px;font-weight:400">We can treated with accupuncher...</h2>
<p class="abs wide">Acupuncture has been used to effectively treat numerous health conditions for thousands of years.&nbsp; According to the World Health Organization, ¼ of the earth’s population receives acupuncture treatment on a continual basis.&nbsp; Both the WHO and the National Institutes of Health endorse acupuncture for many common problems including:</p>

<div class="abs" style="left:45px;top:748px;line-height:24px"><div class="cond">Allergies</div><div class="cond">Anxiety</div><div class="cond">Arthritis</div><div class="cond">Asthma</div><div class="cond">Addictions</div></div>
<div class="abs" style="left:146px;top:748px;line-height:24px"><div class="cond">Carpal Tunnel Syndrome</div><div class="cond">Chronic Fatigue</div><div class="cond">Colitis</div><div class="cond">Common cold</div><div class="cond">Constipation/Diarrhea</div></div>
<div class="abs" style="left:318px;top:748px;line-height:24px"><div class="cond">Depression</div><div class="cond">Digestive issues</div><div class="cond">Dizziness</div><div class="cond">Emotional issues</div><div class="cond">Fatigue</div></div>
<div class="abs" style="left:462px;top:748px;line-height:24px"><div class="cond">Fertility</div><div class="cond">Fibromyalgia</div><div class="cond">Headaches/Migraines</div><div class="cond">Irritable Bowel Syndrome (IBS)</div><div class="cond">Insomnia</div></div>
<div class="abs" style="left:651px;top:748px;line-height:24px"><div class="cond">Low back pain</div><div class="cond">Menopause</div><div class="cond">Menstrual irregularities</div><div class="cond">Osteoarthritis</div><div class="cond">Pain</div></div>
<div class="abs" style="left:808px;top:748px;line-height:24px"><div class="cond">PMS</div><div class="cond">Sciatica</div><div class="cond">Shoulder pain</div><div class="cond">Sinusitis</div><div class="cond">Smoking</div></div>
<div class="abs cond" style="left:45px;top:863px">Stress</div>
<div class="abs cond" style="left:146px;top:863px">Tennis/Golf elbow</div>
<div class="abs cond" style="left:318px;top:863px">Trigeminal neuralgia</div>
<div class="abs cond" style="left:462px;top:863px">Urinary tract infections</div>

<div class="abs rule"></div>
<h2 class="abs store-title" style="font-weight:400">Online Product Store</h2>
<svg class="abs" style="left:900px;top:918px" width="36" height="17"><polyline points="11,2 4,8.5 11,15" fill="none" stroke="#8a8a8a" stroke-width="3"/><polyline points="25,2 32,8.5 25,15" fill="none" stroke="#8a8a8a" stroke-width="3"/></svg>

<div class="abs product-img" style="left:38px"><span role="img" aria-label="Product photo: ear seed patch sheets" style="background:linear-gradient(135deg,#e9d8c8,#c9a88a)"></span></div>
<div class="abs product-title" style="left:167px">Excepteur sint occaecat</div>
<p class="abs product-text" style="left:167px">cupidatat non proident, sunt in culpa qui officia deserunt</p>
<div class="abs view" style="left:167px">View this</div>
<div class="abs buy" style="left:238px">Buy Now</div>

<div class="abs product-img" style="left:344px"><span role="img" aria-label="Product photo: electronic stimulation device" style="background:linear-gradient(135deg,#5870a8,#27396a)"></span></div>
<div class="abs product-title" style="left:473px">Excepteur sint occaecat</div>
<p class="abs product-text" style="left:473px">cupidatat non proident, sunt in culpa qui officia deserunt</p>
<div class="abs view" style="left:473px">View this</div>
<div class="abs buy" style="left:544px">Buy Now</div>

<div class="abs product-img" style="left:647px"><span role="img" aria-label="Product photo: acupuncture needles" style="background:linear-gradient(135deg,#f4f4f4,#d9cfc4)"></span></div>
<div class="abs product-title" style="left:776px">Excepteur sint occaecat</div>
<p class="abs product-text" style="left:776px">cupidatat non proident, sunt in culpa qui officia deserunt</p>
<div class="abs view" style="left:776px">View this</div>
<div class="abs buy" style="left:847px">Buy Now</div>

<footer class="abs footer"></footer>
<div class="abs footer-links">Home<span>|</span>SO Tai Ho<span>|</span>Service<span>|</span>Seitai Shinpo<span>|</span>Acupuncture<span>|</span>Biography<span>|</span>Nutrition<span>|</span>My Journey<span>|</span>Contact Us<span>|</span>Online Store<span>|</span>My Account<span>|</span>Sitemap</div>
<div class="abs pay" style="left:37px"></div>
<div class="abs pay" style="left:70px"></div>
<div class="abs pay" style="left:103px"></div>
<div class="abs pay" style="left:136px"></div>
<div class="abs pay" style="left:170px"></div>
<div class="abs copy">Copyright © 2012 www.lotusridgeacupuncture.com&nbsp;&nbsp; All rights reserved</div>
<div class="abs social" style="left:801px"></div>
<div class="abs social" style="left:828px"></div>
<div class="abs social" style="left:855px"></div>
<div class="abs social" style="left:882px"></div>
<div class="abs social" style="left:910px"></div>
</body>
</html>
```